Computer consultant business card

Bexil Software is a newly started computer consulting company. It's a small one-man company that provides mostly Vornix applications but also websites in collaboration with designers. I'm running this company on the side of full time university studies.

I want the final design to be clean and memorable. Be creative! :)

Some inspiration:
http://www.pixelmarta.com/design/48317
http://www.pixelmarta.com/design/2739164/business-card-design-by-frostlynk
http://www.pixelmarta.com/design/604281/business-card-design-by-koralind-vestrabanu

See attachment for my company logo.
Updates

I would like to thank everyone for submitting! I'll need a couple of days to review and ultimately select a design.

Target Market(s)

Non-technical entrepreneurs and small companies.

Industry/Entity Type

University

Requirements
Must have
• My company logo.
In any way, both colors from my logo.
First- and last name, e-mail and phone number.
Double-sided design.
Nice to have
• Something creative with the symbol in my logo

```html
<!DOCTYPE html>
<html lang="en">
<head>
<meta charset="utf-8">
<title>Bexil Software – Business Card</title>
<link rel="stylesheet" href="https://fonts.googleapis.com/css2?family=Questrial&display=swap">
<style>
  :root {
    --brand-blue: #3f78ff;
    --band-black: #070909;
    --card-mid: #1e2224;
    --card-edge: #0c0d0e;
    --wordmark-grey: #232627;
    --text-white: #ffffff;
    --divider: #9a9d9f;
  }
  * { margin: 0; padding: 0; box-sizing: border-box; }
  html, body {
    width: 1041px;
    height: 1200px;
    overflow: hidden;
    background: var(--card-edge);
    font-family: "Questrial", sans-serif;
  }
  .sheet { position: relative; width: 1041px; height: 1200px; }
  .card-face {
    position: absolute;
    left: 0;
    width: 1041px;
    background: radial-gradient(ellipse 60% 55% at 50% 45%, var(--card-mid) 0%, var(--card-edge) 100%);
  }
  .card-front { top: 0; height: 598px; }
  .card-back { top: 600px; height: 600px; }
  .face-divider {
    position: absolute;
    top: 598px;
    left: 28px;
    width: 986px;
    height: 1px;
    background: var(--divider);
  }
  .dark-band {
    position: absolute;
    background: var(--band-black);
    box-shadow: 0 4px 10px rgba(0,0,0,0.6);
  }
  .blue-tab {
    position: absolute;
    right: 0;
    width: 239px;
    height: 133px;
    background: var(--brand-blue);
    display: flex;
    align-items: center;
    justify-content: center;
  }
  .tab-name {
    font-size: 56px;
    line-height: 1;
    color: var(--band-black);
    letter-spacing: 1px;
  }
  /* front */
  .front-band { top: 233px; left: 0; width: 797px; height: 133px; }
  .front-tab { top: 233px; }
  .brand-dot {
    position: absolute;
    top: 164px;
    left: 60px;
    width: 274px;
    height: 274px;
    border-radius: 50%;
    background: var(--brand-blue);
    box-shadow: 0 6px 16px rgba(0,0,0,0.55);
  }
  .brand-name {
    position: absolute;
    top: 240px;
    left: 384px;
    font-size: 110px;
    line-height: 110px;
    color: var(--wordmark-grey);
    letter-spacing: 2px;
  }
  /* back */
  .name-band { top: 234px; left: 0; width: 411px; height: 132px; }
  .back-tab { top: 234px; }
  .person-name {
    position: absolute;
    top: 264px;
    left: 37px;
    font-size: 60px;
    line-height: 70px;
    font-weight: 400;
    color: var(--text-white);
    letter-spacing: 1px;
    word-spacing: 10px;
  }
  .contact-list {
    position: absolute;
    top: 262px;
    left: 429px;
    list-style: none;
    color: var(--text-white);
    font-size: 25px;
    line-height: 38px;
  }
</style>
</head>
<body>
<main class="sheet">
  <section class="card-face card-front" aria-label="Card front">
    <div class="dark-band front-band"></div>
    <div class="brand-dot"></div>
    <p class="brand-name">Bexil</p>
    <div class="blue-tab front-tab"><span class="tab-name">Bexil</span></div>
  </section>

  <div class="face-divider"></div>

  <section class="card-face card-back" aria-label="Card back">
    <div class="dark-band name-band"></div>
    <h1 class="person-name">Your Name</h1>
    <ul class="contact-list">
      <li>Phone : 1234567890</li>
      <li>Email : yourname@mailvo.com</li>
    </ul>
    <div class="blue-tab back-tab"><span class="tab-name">Bexil</span></div>
  </section>
</main>
</body>
</html>
```